Business Card for Coastal Tundrabridge Advisory

We need a business card for Coastal Tundrabridge Advisory. The company website address is provided below. The company logo is attached. We provide specialized permafrost services to the mining, transportation, and oil & gas industries. The card should be prepared for:
Matthias Korhonen, PhD.
Coastal Tundrabridge Advisory
PO Box 418259
Quillwater, Alaska 99642
Direct: +1-907-555-0143
Email: mkorhonen@tundrabridgeadvisory.example
Website: www.coastaltundrabridgeadvisory.example

```html
<!DOCTYPE html>
<html lang="en">
<head>
<meta charset="utf-8">
<title>Coastal Tundrabridge Advisory — Business Card</title>
<link rel="stylesheet" href="https://fonts.googleapis.com/css2?family=Open+Sans:wght@300;400;600;700&display=swap">
<style>
  :root {
    --stage: #232323;
    --card: #0f1520;
    --card-deep: #0b1019;
    --ink: #ffffff;
    --ink-soft: #c9ced6;
    --ink-faint: #1c2431;
    --ice: #3fa3dc;
    --ice-deep: #15405c;
  }
  * { margin: 0; padding: 0; box-sizing: border-box; }
  html, body {
    width: 1200px; height: 780px; overflow: hidden;
    background: var(--stage);
    font-family: "Open Sans", Arial, sans-serif;
  }
  .stage {
    position: relative; width: 1200px; height: 780px;
    display: flex; align-items: center; justify-content: center; gap: 40px;
  }
  .card {
    position: relative; width: 540px; height: 309px;
    background: var(--card); overflow: hidden;
    box-shadow: 0 18px 40px rgba(0,0,0,.55);
  }

  /* ---------- front ---------- */
  .wordmark {
    position: absolute; left: 28px; top: 26px;
    color: var(--ink); font-weight: 700; font-size: 19px;
    letter-spacing: .5px; line-height: 1.15;
  }
  .wordmark small {
    display: block; font-size: 8px; font-weight: 400;
    letter-spacing: 4px; text-transform: uppercase; color: var(--ink-soft);
  }
  .contact {
    position: absolute; left: 28px; top: 140px;
    color: var(--ink-soft); font-size: 10.5px; line-height: 1.55; font-weight: 400;
  }
  .contact .address { margin-bottom: 8px; }
  .contact ul { list-style: none; }
  .contact li { display: flex; align-items: center; gap: 8px; }
  .contact svg { width: 11px; height: 11px; fill: none; stroke: var(--ink); stroke-width: 1.6; flex: none; }
  .holder {
    position: absolute; right: 36px; top: 112px; text-align: right; color: var(--ink);
  }
  .holder-name { font-size: 24px; line-height: 1.1; }
  .holder-name b { font-weight: 700; }
  .holder-name span { font-weight: 300; }
  .holder-title { font-size: 13px; font-weight: 600; margin-top: 2px; }
  .edge-bar {
    position: absolute; right: 0; top: 112px; width: 18px; height: 44px; background: var(--ink);
  }
  .faint-mark {
    position: absolute; right: 22px; bottom: 22px;
    color: var(--ink-faint); font-weight: 700; font-size: 30px; letter-spacing: 1px;
  }

  /* ---------- back ---------- */
  .card-back { background: var(--card-deep); }
  .pattern-field {
    position: absolute; inset: 0;
    background: linear-gradient(100deg, var(--card-deep) 0%, #111a26 45%, var(--ice-deep) 72%, var(--ice) 100%);
    opacity: .85;
  }
  .back-mark {
    position: absolute; left: 50%; top: 92px; transform: translateX(-50%);
    text-align: center; color: var(--ink); font-weight: 700; font-size: 24px; white-space: nowrap;
  }
  .back-mark small {
    display: block; font-size: 9px; font-weight: 400; letter-spacing: 5px;
    text-transform: uppercase; margin-top: 4px;
  }
  .services {
    position: absolute; left: 28px; right: 28px; bottom: 30px;
    color: var(--ink-soft); text-align: center;
  }
  .services h2 { font-size: 11px; font-weight: 600; color: var(--ink); letter-spacing: .5px; margin-bottom: 4px; }
  .services p { font-size: 10.5px; font-style: italic; }
</style>
</head>
<body>
<main class="stage">

  <section class="card card-front" aria-label="Card front">
    <div class="wordmark">Coastal Tundrabridge<small>Advisory</small></div>

    <div class="holder">
      <div class="holder-name"><b>Matthias</b> <span>Korhonen</span></div>
      <div class="holder-title">PhD</div>
    </div>
    <div class="edge-bar"></div>

    <div class="contact">
      <div class="address">PO Box 418259<br>Quillwater, Alaska 99642</div>
      <ul>
        <li><svg viewBox="0 0 12 12"><path d="M3 1.5l1.6 2.3-1 1.2a6 6 0 0 0 3.4 3.4l1.2-1 2.3 1.6-.8 1.7C5 10.5 1.5 7 1.3 2.3z"/></svg>+1-907-555-0143</li>
        <li><svg viewBox="0 0 12 12"><rect x="1" y="2.5" width="10" height="7"/><path d="M1 2.5l5 4 5-4"/></svg>mkorhonen@tundrabridgeadvisory.example</li>
        <li><svg viewBox="0 0 12 12"><circle cx="6" cy="6" r="4.8"/><path d="M1.2 6h9.6M6 1.2c-2.4 3-2.4 6.6 0 9.6M6 1.2c2.4 3 2.4 6.6 0 9.6"/></svg>www.coastaltundrabridgeadvisory.example</li>
      </ul>
    </div>

    <div class="faint-mark">Coastal Tundrabridge</div>
  </section>

  <section class="card card-back" aria-label="Card back">
    <div class="pattern-field" role="img" aria-label="Repeating company name pattern fading from dark navy to ice blue"></div>
    <div class="back-mark">Coastal Tundrabridge<small>Advisory</small></div>
    <div class="services">
      <h2>OUR SERVICES</h2>
      <p>We provide specialized permafrost services to the mining, transportation, and oil &amp; gas industries</p>
    </div>
  </section>

</main>
</body>
</html>
```